Envelope Design - Winner can do follow-up business

- Varnoko.com is a Swiss-based online store selling business shirts and accessories for business men
- Please visit the webpage to make yourself familiar with the company. Although the text is in German, with Plimbo translator you should be able to understand the main content.
- Our clients are mainly business men between 30 and 60 years old. Mostly with a high income working in the service industry (banking, insurance, lawyers, etc.). Sometimes there wives purchase the shirts for them ;-)
- The colors and the logo are given, as they are also used for the print materials (please see files in attachment)
- I am running several businesses and often need a talented web designer --> the winner gets substantial follow-up business
your task:
-for our company we need a new envelope design
-It should be simple and modern
-please use one of the logos in the followings.
-suprise me :)

```html
<!DOCTYPE html>
<html lang="en">
<head>
<meta charset="utf-8">
<title>Varnoko Envelope Set</title>
<link rel="stylesheet" href="https://fonts.googleapis.com/css2?family=Montserrat:wght@500;600&family=Open+Sans:wght@400&display=swap">
<style>
  :root {
    --backdrop: #4a3324;
    --paper: #ffffff;
    --ink-black: #000000;
    --brand-red: #ee2e24;
    --brand-gold: #e4d46c;
    --text-dark: #1a1a1a;
    --edge: #c9c9c9;
  }
  html, body {
    margin: 0;
    padding: 0;
    width: 1200px;
    height: 889px;
    overflow: hidden;
    background: var(--backdrop);
  }
  .stage {
    position: relative;
    width: 1200px;
    height: 889px;
  }
  .envelope {
    position: absolute;
    background: var(--paper);
    box-shadow: 0 2px 6px rgba(0,0,0,0.35);
  }
  .envelope-back-black { left: 189px; top: 48px; width: 937px; height: 610px; }
  .envelope-back-red { left: 100px; top: 214px; width: 938px; height: 441px; border: 1px solid var(--edge); box-sizing: border-box; }
  .envelope-front { left: 214px; top: 407px; width: 938px; height: 442px; display: flex; }
  .flap {
    position: absolute;
    left: 0;
    top: 0;
    display: block;
  }
  .flap-name {
    position: absolute;
    left: 0;
    width: 100%;
    text-align: center;
    font-family: "Montserrat", sans-serif;
    font-weight: 600;
    color: var(--paper);
    letter-spacing: 2px;
    margin: 0;
  }
  .envelope-back-black .flap-name { top: 28px; font-size: 27px; }
  .envelope-back-red .flap-name { top: 66px; font-size: 34px; }
  .front-panel {
    width: 335px;
    height: 100%;
    background: var(--ink-black);
    position: relative;
  }
  .front-name {
    position: absolute;
    top: 98px;
    left: 0;
    width: 100%;
    text-align: center;
    margin: 0;
    font-family: "Montserrat", sans-serif;
    font-weight: 500;
    font-size: 40px;
    letter-spacing: 3px;
    color: var(--brand-gold);
  }
  .front-web {
    position: absolute;
    bottom: 20px;
    left: 0;
    width: 100%;
    display: flex;
    justify-content: center;
    align-items: center;
    gap: 10px;
    font-family: "Open Sans", sans-serif;
    font-size: 19px;
    color: var(--paper);
  }
  .front-address-area {
    flex: 1;
    position: relative;
  }
  .front-address {
    position: absolute;
    right: 30px;
    bottom: 20px;
    display: flex;
    align-items: center;
    gap: 12px;
    font-family: "Open Sans", sans-serif;
    font-size: 19px;
    color: var(--text-dark);
  }
</style>
</head>
<body>
<main class="stage">
  <section class="envelope envelope-back-black" aria-label="Envelope back, black flap">
    <svg class="flap" width="937" height="150" viewBox="0 0 937 150">
      <path d="M0,0 H937 L926,28 Q912,72 860,80 L520,144 Q469,154 418,144 L77,80 Q25,72 11,28 Z" fill="var(--ink-black)"/>
    </svg>
    <p class="flap-name">VARNOKO</p>
  </section>

  <section class="envelope envelope-back-red" aria-label="Envelope back, red flap">
    <svg class="flap" width="936" height="152" viewBox="0 0 936 152">
      <path d="M0,0 H936 L925,30 Q910,74 858,82 L520,145 Q468,156 416,145 L78,82 Q26,74 11,30 Z" fill="var(--brand-red)"/>
    </svg>
    <p class="flap-name">VARNOKO</p>
  </section>

  <section class="envelope envelope-front" aria-label="Envelope front">
    <div class="front-panel">
      <p class="front-name">VARNOKO</p>
      <div class="front-web">
        <svg width="22" height="22" viewBox="0 0 22 22" aria-hidden="true">
          <g fill="none" stroke="#fff" stroke-width="1.4">
            <circle cx="11" cy="11" r="9.5"/>
            <ellipse cx="11" cy="11" rx="4.2" ry="9.5"/>
            <line x1="1.5" y1="11" x2="20.5" y2="11"/>
            <path d="M3.2,6 H18.8 M3.2,16 H18.8"/>
          </g>
        </svg>
        <span>www.varnoko.com</span>
      </div>
    </div>
    <div class="front-address-area">
      <div class="front-address">
        <svg width="18" height="24" viewBox="0 0 18 24" aria-hidden="true">
          <path d="M9,0 C4,0 0,4 0,9 C0,15 9,24 9,24 C9,24 18,15 18,9 C18,4 14,0 9,0 Z" fill="var(--brand-red)"/>
          <circle cx="9" cy="9" r="3.4" fill="#fff"/>
        </svg>
        <span>Street Name, City Name, State Zipcode</span>
      </div>
    </div>
  </section>
</main>
</body>
</html>
```